Managed IT services business card design

We haven't needed a business card since the founding of the business in 2005. All our clients have been coming through word of mouth. And lately more and more existing clients are requesting for our business cards to pass on to their contacts in recommending us.
So we needing a business card design. We use various innovative solutions and methodologies to provide IT services to small businesses in managing their IT systems. Our role is the same as an in-house, full-time IT Manager for our clients, but outsourced. So we take care of all our clients' IT needs, just as an IT Manager would be expected to perform.
We have a holding website, which we're happy to leave for now. If we can use the same logo would be great - www.lumadesk.com.au
Preferred colours are shades of are white, grey and black.
We pride our business with the following traits: proactive, good service, prompt response, trustworthy.
Target Market(s)
Small businesses of any industry
Industry/Entity Type
Business

```html
<!DOCTYPE html>
<html lang="en">
<head>
<meta charset="utf-8">
<title>Lumadesk Business Card</title>
<link rel="stylesheet" href="https://fonts.googleapis.com/css2?family=Arimo:wght@400&family=Questrial&display=swap">
<style>
  :root {
    --backdrop: #e4e4e4;
    --ink-dark: #2b2624;
    --paper: #ffffff;
    --band-grey: #5f6466;
    --rule: #3a3a3a;
    --text-dark: #1e1e1e;
    --text-mid: #555555;
  }
  * { box-sizing: border-box; margin: 0; padding: 0; }
  html, body {
    width: 1200px; height: 680px; overflow: hidden;
    background: var(--backdrop);
  }
  .sheet {
    position: relative; width: 1200px; height: 680px;
    display: flex; align-items: center; justify-content: center; gap: 50px;
  }
  .card {
    position: relative; width: 520px; height: 297px;
    border-radius: 22px; overflow: hidden;
    box-shadow: 0 6px 18px rgba(0,0,0,0.18);
  }

  /* Front */
  .card-front { background: var(--ink-dark); }
  .card-front .brand {
    position: absolute; left: 0; right: 0; top: 108px;
    text-align: center;
    font-family: "Questrial", sans-serif; font-size: 52px;
    letter-spacing: 0.28em; color: var(--paper);
  }
  .web-tab {
    position: absolute; right: 0; bottom: 0;
    width: 240px; height: 36px;
    border-top-left-radius: 22px;
    display: flex; align-items: center; justify-content: center;
    font-family: "Arimo", sans-serif; font-size: 13px; letter-spacing: 0.22em;
  }
  .card-front .web-tab { background: var(--paper); color: var(--text-dark); }

  /* Back */
  .card-back { background: var(--paper); }
  .card-back .brand {
    position: absolute; left: 34px; top: 92px;
    font-family: "Questrial", sans-serif; font-size: 36px;
    letter-spacing: 0.26em; color: var(--text-dark);
  }
  .divider {
    position: absolute; left: 34px; right: 34px; top: 150px;
    height: 1px; background: var(--rule);
  }
  .person {
    position: absolute; right: 34px; top: 100px; text-align: right;
    font-family: "Arimo", sans-serif;
  }
  .person-name { font-size: 17px; color: var(--text-dark); letter-spacing: 0.03em; }
  .person-role { font-size: 12px; color: var(--text-mid); margin-top: 2px; }
  .address {
    position: absolute; right: 34px; top: 164px; text-align: right;
    font-family: "Arimo", sans-serif; font-size: 13px; line-height: 1.35;
    color: var(--text-dark);
  }
  .contacts {
    position: absolute; left: 34px; top: 168px; list-style: none;
    font-family: "Arimo", sans-serif; font-size: 15px; color: var(--text-dark);
  }
  .contacts li { display: flex; align-items: center; gap: 10px; line-height: 22px; }
  .contacts svg { width: 14px; height: 14px; flex: none; }
  .grey-band {
    position: absolute; left: 0; bottom: 0; width: 300px; height: 16px;
    background: var(--band-grey);
  }
  .card-back .web-tab { background: var(--ink-dark); color: var(--paper); }
</style>
</head>
<body>
<main class="sheet">
  <section class="card card-front" aria-label="Card front">
    <div class="brand">lumadesk</div>
    <div class="web-tab">www.lumadesk.com.au</div>
  </section>

  <section class="card card-back" aria-label="Card back">
    <div class="brand">lumadesk</div>
    <div class="person">
      <p class="person-name">Mark Ellison</p>
      <p class="person-role">director</p>
    </div>
    <div class="divider"></div>
    <address class="address">
      1450 Kent Vale Rd<br>Selby TX 78010
    </address>
    <ul class="contacts">
      <li>
        <svg viewBox="0 0 16 16" aria-hidden="true"><path d="M4 1.5 6.5 4 5 6c.8 2 2.6 3.8 4.6 4.6l2-1.5 2.5 2.5-1.7 2.2C7.5 13.5 2.4 8.4 1.8 3.2z" fill="#333"/></svg>
        512 004 2700
      </li>
      <li>
        <svg viewBox="0 0 16 16" aria-hidden="true"><rect x="4" y="1.5" width="8" height="5" fill="none" stroke="#333" stroke-width="1.4"/><rect x="1.5" y="6" width="13" height="6" rx="1" fill="#333"/><rect x="4" y="10" width="8" height="4.5" fill="#fff" stroke="#333" stroke-width="1.2"/></svg>
        512 004 2701
      </li>
      <li>
        <svg viewBox="0 0 16 16" aria-hidden="true"><rect x="1.5" y="3.5" width="13" height="9" fill="none" stroke="#333" stroke-width="1.4"/><path d="M1.5 3.5 8 9l6.5-5.5" fill="none" stroke="#333" stroke-width="1.4"/></svg>
        info@lumadesk.com.au
      </li>
    </ul>
    <div class="grey-band"></div>
    <div class="web-tab">www.lumadesk.com.au</div>
  </section>
</main>
</body>
</html>
```